Business price tag design for Furniture Business

Hello,

I have developed a tag for a home furniture business and need 1 more creative template. Please see attachment. I need the template to be very appealing.

Requirements:

1.Tag dimensions needs to be about the same as attached tag.
2. Tag design needs to be suitable for a home furniture business.
3. Tag needs to have locations for the following: Item Title, Now Price, Was Price, Product Number.
4. "The black shape at the bottom of attached tag could be removed.

I have no requirements on colors, but something professional is needed, preferably white background to reduce print ink consumption.

Please see attachment for clarification.

Industry/Entity Type

Retail

Font styles to use
Serif
Sans Serif

Requirements
Must have
• Please see Project Description.
Nice to have

```html
<!DOCTYPE html>
<html lang="en">
<head>
<meta charset="utf-8">
<title>Harbor Furniture Outlet – Price Tag</title>
<link href="https://fonts.googleapis.com/css2?family=Oswald:wght@300;400;500;600;700&display=swap" rel="stylesheet">
<style>
  :root {
    --coral: #ef6a4f;
    --red: #ea5a3e;
    --cream: #f8f3e6;
    --cream-ray: #efe6d0;
    --brown: #5b3a2d;
    --white: #ffffff;
    --art-warm: #f2b04a;
    --art-deep: #d9573d;
  }
  html, body {
    margin: 0;
    padding: 0;
    width: 1200px;
    height: 2416px;
    overflow: hidden;
    background: var(--coral);
  }
  .price-tag {
    position: relative;
    width: 1200px;
    height: 2416px;
    background: var(--coral);
    font-family: "Oswald", sans-serif;
    color: var(--brown);
  }
  .panel {
    position: absolute;
    left: 64px;
    width: 1072px;
    background: radial-gradient(circle at 50% 55%, var(--cream) 0%, var(--cream) 45%, var(--cream-ray) 100%);
    overflow: hidden;
  }
  .panel-brand { top: 40px; height: 992px; }
  .panel-price { top: 1152px; height: 1208px; }
  .corner {
    position: absolute;
    width: 288px;
    height: 288px;
    border-radius: 50%;
    background: var(--coral);
  }
  .corner-top-left { left: -144px; top: -144px; }
  .corner-bottom-right { right: -160px; bottom: -160px; width: 320px; height: 320px; }
  .product-art {
    position: absolute;
    left: 196px;
    top: 112px;
    width: 680px;
    height: 548px;
    border-radius: 24px;
    background: linear-gradient(160deg, var(--art-warm) 0%, var(--art-deep) 100%);
  }
  .brand-name {
    position: absolute;
    left: 0;
    width: 100%;
    top: 648px;
    margin: 0;
    text-align: center;
    font-size: 150px;
    font-weight: 700;
    line-height: 1;
    color: var(--red);
    letter-spacing: 2px;
  }
  .brand-tagline {
    position: absolute;
    left: 0;
    width: 100%;
    top: 850px;
    margin: 0;
    text-align: center;
    font-size: 66px;
    font-weight: 500;
    line-height: 1;
    color: var(--brown);
  }
  .item-title-band {
    position: absolute;
    left: 64px;
    top: 1032px;
    width: 1072px;
    height: 104px;
    background: var(--red);
    color: var(--white);
    font-size: 76px;
    font-weight: 500;
    line-height: 104px;
    text-align: center;
    margin: 0;
  }
  .product-number {
    position: absolute;
    left: 156px;
    top: 52px;
    font-size: 74px;
    font-weight: 500;
    line-height: 1;
  }
  .compare-label {
    position: absolute;
    left: 156px;
    top: 208px;
    font-size: 116px;
    font-weight: 300;
    line-height: 1;
  }
  .was-price {
    position: absolute;
    left: 156px;
    top: 420px;
    font-size: 104px;
    font-weight: 600;
    line-height: 1;
  }
  .now-label {
    position: absolute;
    left: 156px;
    top: 640px;
    font-size: 124px;
    font-weight: 600;
    line-height: 1;
  }
  .now-price {
    position: absolute;
    left: 640px;
    top: 628px;
    width: 432px;
    height: 240px;
    background: var(--red);
    color: var(--white);
    font-size: 134px;
    font-weight: 500;
    line-height: 240px;
    text-align: center;
  }
  .savings {
    position: absolute;
    left: 156px;
    top: 1000px;
    font-size: 74px;
    font-weight: 600;
    line-height: 1;
  }
</style>
</head>
<body>
  <main class="price-tag">
    <section class="panel panel-brand">
      <div class="corner corner-top-left"></div>
      <div class="product-art" role="img" aria-label="Illustration of assorted home furniture: sofa, armchair, wardrobe, lamps and side tables"></div>
      <h1 class="brand-name">HARBOR</h1>
      <p class="brand-tagline">FURNITURE OUTLET</p>
    </section>

    <h2 class="item-title-band">Black Queen Bed</h2>

    <section class="panel panel-price">
      <div class="product-number">B4350</div>
      <div class="compare-label">COMPARE</div>
      <div class="was-price">AT:&nbsp;&nbsp;$ 500</div>
      <div class="now-label">Only for</div>
      <div class="now-price">$ 450</div>
      <div class="savings">You Save: $50</div>
      <div class="corner corner-bottom-right"></div>
    </section>
  </main>
</body>
</html>
```